Dynamic Business Card for Sports Supplements Company

Hi! I'm looking for an awesome business card to match my existing sports supplement company. I have uploaded my current company logo and screenshot of the front page of my website.

I would like to have something dynamic and interesting and utilize the colors in the website - the reds and purples

The business card should be double sided and focus on a unique eye-catching design on the back and include all the relevant company info.

Most importantly, it should say somewhere: "Sign up on our website for a coupon code."

Target Market(s)

Mostly for women gym goers but it shouldn't be too feminine. It should be in keeping with the website design. It should flow and clearly be connected to it

Industry/Entity Type

Business

Contact Information for Business Card

Lorraine K. Vestal
CEO
LVestal@Quorvanexco.com
www.quorvanexco.com
555.417.3820
P.O. Box 47315
Dunmore, Vermont 00000

Sign up on our website for a coupon code

Font styles to use
Serif
Sans Serif
Other font styles liked:
• Novecento font family and "Quorvanex" is in AR Destine font

Requirements
Must have
• One side should be a bold Quorvanex logo design. Even just the symbol itself may be o.k. (see attached file)

```html
<!DOCTYPE html>
<html lang="en">
<head>
<meta charset="utf-8">
<title>Quorvanex Business Card</title>
<link rel="stylesheet" href="https://fonts.googleapis.com/css2?family=Montserrat:wght@400;600;700&display=swap">
<style>
  :root {
    --backdrop: #3b3b3d;
    --card-black: #050505;
    --card-white: #ffffff;
    --ink: #111111;
    --muted: #7a7a7a;
    --accent-red: #e3222a;
    --paper-text: #f2f2f2;
  }
  * { margin: 0; padding: 0; box-sizing: border-box; }
  html, body {
    width: 1200px; height: 855px; overflow: hidden;
    background: var(--backdrop);
    font-family: "Montserrat", sans-serif;
  }
  .canvas {
    width: 1200px; height: 855px;
    display: flex; flex-direction: column;
    align-items: center; justify-content: center; gap: 40px;
  }
  .card {
    width: 620px; height: 354px; position: relative;
    box-shadow: 0 10px 28px rgba(0,0,0,0.45);
  }
  /* Back side */
  .card-back { background: var(--card-black); color: var(--paper-text); }
  .back-brand {
    position: absolute; top: 120px; left: 0; right: 0;
    display: flex; align-items: center; justify-content: center; gap: 14px;
  }
  .brand-dot {
    width: 22px; height: 22px; border-radius: 50%;
    background: var(--accent-red);
  }
  .back-brand .brand-name {
    font-size: 40px; font-weight: 700; letter-spacing: 4px; color: var(--paper-text);
  }
  .coupon-note {
    position: absolute; bottom: 44px; left: 0; right: 0;
    text-align: center; font-size: 15px; font-weight: 400; letter-spacing: 0.6px;
  }
  /* Front side */
  .card-front { background: var(--card-white); color: var(--ink); }
  .front-brand {
    position: absolute; top: 60px; right: 42px; text-align: right;
  }
  .front-brand .brand-name {
    font-size: 34px; font-weight: 700; letter-spacing: 3px; color: var(--ink);
  }
  .tagline {
    font-size: 10.5px; font-weight: 400; letter-spacing: 1.4px; margin-top: 2px;
  }
  .contact-block { position: absolute; left: 44px; top: 168px; }
  .person-name { font-size: 21px; font-weight: 600; color: var(--ink); }
  .person-title { font-size: 14px; color: var(--muted); margin-top: 2px; }
  .address { font-size: 14px; color: var(--muted); margin-top: 14px; line-height: 1.35; }
  .contact-list { list-style: none; margin-top: 12px; }
  .contact-list li {
    display: flex; align-items: center; gap: 9px;
    font-size: 14px; color: var(--muted); line-height: 1.55;
  }
  .contact-list svg { width: 14px; height: 14px; flex: none; }
</style>
</head>
<body>
<main class="canvas">
  <section class="card card-back" aria-label="Card back">
    <div class="back-brand">
      <span class="brand-dot"></span>
      <span class="brand-name">QUORVANEX</span>
    </div>
    <p class="coupon-note">Sign up on our website for a coupon code</p>
  </section>

  <section class="card card-front" aria-label="Card front">
    <div class="front-brand">
      <div class="brand-name">QUORVANEX</div>
      <div class="tagline">YOUR TRAINING TEAMMATE</div>
    </div>
    <div class="contact-block">
      <h1 class="person-name">Lorraine K. Vestal</h1>
      <p class="person-title">CEO</p>
      <p class="address">P.O. Box 47315<br>Dunmore, Vermont 00000</p>
      <ul class="contact-list">
        <li>
          <svg viewBox="0 0 24 24" aria-hidden="true"><path fill="var(--accent-red)" d="M6.6 10.8a15 15 0 0 0 6.6 6.6l2.2-2.2a1 1 0 0 1 1-.25 11.4 11.4 0 0 0 3.6.57 1 1 0 0 1 1 1V20a1 1 0 0 1-1 1A17 17 0 0 1 3 4a1 1 0 0 1 1-1h3.5a1 1 0 0 1 1 1c0 1.25.2 2.45.57 3.6a1 1 0 0 1-.25 1z"/></svg>
          555.417.3820
        </li>
        <li>
          <svg viewBox="0 0 24 24" aria-hidden="true"><rect x="2" y="5" width="20" height="14" fill="var(--accent-red)"/><path d="M2 5l10 8 10-8" fill="none" stroke="#fff" stroke-width="2"/></svg>
          LVestal@Quorvanexco.com
        </li>
        <li>
          <svg viewBox="0 0 24 24" aria-hidden="true"><g fill="none" stroke="var(--accent-red)" stroke-width="2"><circle cx="12" cy="12" r="9"/><ellipse cx="12" cy="12" rx="4" ry="9"/><path d="M3 12h18M5 7h14M5 17h14"/></g></svg>
          www.quorvanexco.com
        </li>
      </ul>
    </div>
  </section>
</main>
</body>
</html>
```